brovlanepass.net

Develop a website for brolanepass.net will be a site to sell tickets for concerts, shows, shows, theaters and others. I need a web design easy view, very easy to use and accumulate events by date. The aim is to develop the site was connected to a complex system that is already developed. (Important this page to a robust system was connected via links the idea is to develop only the front view)
Updates

Reason: I need more designs yet we have not made the decision

Target Market(s)

millennials, adults, who want to enjoy concerts and shows

Industry/Entity Type

Event

Number of Pages Required

5+ page

Colors
1b1b1b
aaaaaa
ffffff

Requirements
Must have
• Easy Vista, accumulation of upcoming events, past events. The tabs should have are: 1 Start: In this part of upcoming events occur. You could put a banner on the top and down the events by date. 2. How to order: page with instructions on how to purchase tickets 3. About Us: The company history 4. Contact: Phones and template for contact by mail 5. Our policies: shopping 6. Notice Privacy: Privacy Notice Copoy 7. Centers Sale: physical places where they can purchase tickets Promoters 8. access: Link to a template
Nice to have
• as you can see p www.quimbarostage.net or farunda.net or farunda.org or gallowmerk.net (important this page to a robust system was connected via links the idea is to develop only the front view)
Should not have
• Many things Tangled

```html
<!DOCTYPE html>
<html lang="en">
<head>
<meta charset="utf-8">
<title>Brovlanepass – Access</title>
<link rel="stylesheet" href="https://fonts.googleapis.com/css2?family=Lato:wght@400;700&family=Open+Sans:wght@400;600;700&family=Montserrat:wght@800&display=swap">
<style>
:root{
  --black:#000;
  --ink:#1b1b1b;
  --grey:#aaaaaa;
  --white:#ffffff;
  --red:#e0474c;
  --nav-top:#262626;
  --nav-bottom:#0e0e0e;
  --content-a:#2a0a22;
  --content-b:#1a0716;
  --rule:#4a3a40;
}
*{box-sizing:border-box;margin:0;padding:0}
html,body{width:1200px;height:1168px;overflow:hidden;background:var(--black)}
body{font-family:"Lato",sans-serif;color:var(--white);position:relative}

.site-header{position:absolute;left:0;top:0;width:1200px;height:112px;background:var(--black)}
.phone{position:absolute;left:105px;top:33px;display:flex;align-items:center;gap:14px;font-family:"Open Sans",sans-serif;font-size:22px}
.phone-icon{width:43px;height:43px;border:2px solid var(--white);border-radius:50%;display:flex;align-items:center;justify-content:center}
.brand{position:absolute;display:flex;align-items:center;justify-content:center;gap:10px}
.brand-header{left:525px;top:18px;width:150px;height:76px}
.brand-footer{left:89px;top:87px;width:150px;height:76px}
.brand-mark{display:block;flex-shrink:0;width:14px;height:14px;background:var(--red)}
.brand-name{font-family:"Open Sans",sans-serif;font-weight:700;font-size:19px;color:var(--red);letter-spacing:.3px}
.social{position:absolute;right:102px;top:42px;display:flex;gap:13px}
.social span{width:24px;height:24px;border-radius:4px;background:#1e8fd6}
.social span.alt{background:var(--red)}

.main-nav{position:absolute;left:0;top:112px;width:1200px;height:58px;background:linear-gradient(var(--nav-top),var(--nav-bottom))}
.main-nav ul{list-style:none;display:flex;position:absolute;left:97px;top:0;height:58px}
.main-nav li{height:58px;padding:0 24.5px;display:flex;align-items:center;font-family:"Open Sans",sans-serif;font-size:16px;text-transform:uppercase}
.main-nav li.active{background:var(--black);box-shadow:inset 0 3px 0 var(--red);padding:0 26px}

.page-banner{position:absolute;left:0;top:170px;width:1200px;height:178px;background:linear-gradient(90deg,#141214 0%,#241b20 45%,#3a3540 75%,#1c1a22 100%)}
.page-banner h1{position:absolute;width:100%;top:82px;text-align:center;font-family:"Montserrat",sans-serif;font-weight:800;font-size:35px;line-height:1;letter-spacing:.5px}

.content{position:absolute;left:0;top:348px;width:1200px;height:529px;background:radial-gradient(ellipse at 40% 70%,#3a0d2c 0%,var(--content-a) 40%,var(--content-b) 100%)}
.content h2{position:absolute;left:96px;top:42px;font-family:"Open Sans",sans-serif;font-weight:400;font-size:27px}
.content .copy{position:absolute;left:89px;top:82px;width:1024px;font-size:14.7px;line-height:22.8px;text-align:justify;letter-spacing:-.05px}
.content p+p{margin-top:22.8px}

.site-footer{position:absolute;left:0;top:877px;width:1200px;height:291px;background:linear-gradient(#161014,#120c10)}
.footer-col{position:absolute;top:58px}
.footer-col h3{font-family:"Open Sans",sans-serif;font-weight:400;font-size:16px;text-transform:uppercase;margin-bottom:20px}
.contact-list{font-size:13.5px;line-height:22px;margin-left:2px}
.mail-note{font-family:"Open Sans",sans-serif;font-size:12px;line-height:17px;width:200px;margin-left:1px}
.mail-form{display:flex;margin-top:10px;margin-left:1px}
.mail-form .field{width:146px;height:31px;background:var(--white);color:#777;font-family:"Open Sans",sans-serif;font-size:12px;padding:8px}
.mail-form .submit{width:56px;height:31px;background:#555;color:var(--white);font-family:"Open Sans",sans-serif;font-size:12.5px;display:flex;align-items:center;justify-content:center}
.follow{display:flex;gap:14px;margin-top:8px}
.follow span{width:25px;height:25px;border-radius:4px;background:var(--white)}
.footer-rule{position:absolute;left:87px;top:224px;width:1023px;height:1px;background:var(--rule)}
.copyright{position:absolute;top:250px;width:100%;text-align:center;font-size:13.5px}
</style>
</head>
<body>
<header class="site-header">
  <div class="phone">
    <span class="phone-icon">
      <svg width="20" height="20" viewBox="0 0 24 24"><path fill="#fff" d="M6.6 10.8a15.1 15.1 0 0 0 6.6 6.6l2.2-2.2c.3-.3.7-.4 1-.2 1.1.4 2.3.6 3.6.6.6 0 1 .4 1 1V20c0 .6-.4 1-1 1A17 17 0 0 1 3 4c0-.6.4-1 1-1h3.5c.6 0 1 .4 1 1 0 1.3.2 2.5.6 3.6.1.3 0 .7-.2 1z"/></svg>
    </span>
    <span>+852 5550 1724</span>
  </div>
  <div class="brand brand-header"><span class="brand-mark"></span><span class="brand-name">BROVLANEPASS</span></div>
  <div class="social" aria-label="Social links"><span></span><span></span><span></span><span class="alt"></span></div>
</header>

<nav class="main-nav">
  <ul>
    <li>Home</li><li>How to order</li><li>About us</li><li>Contact us</li><li>Policies</li><li>Privacy</li><li>Center sale</li><li class="active">Access</li>
  </ul>
</nav>

<section class="page-banner" role="img" aria-label="Concert hall audience facing a lit stage">
  <h1>ACCESS</h1>
</section>

<main class="content">
  <h2>ACCESS</h2>
  <div class="copy">
    <p>It is a long established fact that a reader will be distracted by the readable content of a page when looking at its layout. The point of using Lorem Ipsum is that it has a more-or-less normal distribution of letters, as opposed to using 'Content here, content here', making it look like readable English. Many desktop pub&shy;lishing packages and web page editors now use Lorem Ipsum as their default model text, and a search for 'lorem ipsum' will uncover many web sites still in their infancy. Various versions have evolved over the years, sometimes by accident, sometimes on purpose It is a long established fact that a reader will be dis&shy;tracted by the readable content of a page when looking at its layout. The point of using Lorem Ipsum is that it has a more-or-less normal distribution.</p>
    <p>The point of using Lorem Ipsum is that it has a more-or-less normal distribution of letters, as opposed to using 'Content here, content here', making it look like readable English. Many desktop publishing packages and web page editors now use Lorem Ipsum as their default model text, and a search for 'lorem ipsum' will uncover many web sites still in their infancy. Various versions have evolved over the years, sometimes by accident, sometimes on purpose It is a long estab&shy;lished fact that a reader will be distracted by the readable content of a page when looking at its layout. The point of using Lorem Ipsum is that it has a more-or-less normal distribution of letters, as opposed to using 'Content here, content here', making it look like readable English.</p>
    <p>Lorem Ipsum is simply dummy text of the printing and typesetting industry. Lorem Ipsum has been the industry's standard dummy text ever since the 1500s, when an unknown printer took a galley of type and scrambled it to make a type specimen book. It has survived not only five centuries, but also the leap into electronic typesetting, remaining essentially unchanged. It was popularised in the 1960s with the release of Kelvarin sheets containing Lorem Ipsum passages, and more recently with desktop publishing software like Torvane Layout including versions of Lorem Ipsum.</p>
  </div>
</main>

<footer class="site-footer">
  <div class="brand brand-footer"><span class="brand-mark"></span><span class="brand-name">BROVLANEPASS</span></div>
  <div class="footer-col" style="left:343px">
    <h3>Contact us</h3>
    <div class="contact-list">
      Address : 2174 Orvell Ln,<br>Dunmere, Fl, 33190<br>Phone : 555-014-2270<br>Email : hello@brovlanepass.net
    </div>
  </div>
  <div class="footer-col" style="left:642px">
    <h3>Join our mailing list</h3>
    <p class="mail-note">Your about us information would fit here nicely.</p>
    <div class="mail-form"><span class="field">Email address</span><span class="submit">Submit</span></div>
  </div>
  <div class="footer-col" style="left:941px">
    <h3>Follow us out there</h3>
    <div class="follow" aria-label="Social links"><span></span><span></span><span></span><span></span></div>
  </div>
  <div class="footer-rule"></div>
  <p class="copyright">Copyright © 2017. All Rights Reserved</p>
</footer>
</body>
</html>
```